Corvane Freight Company Business Card Design

We are a company that delivers natural saltwater (from the ocean) to aquarium companies, restaurants and home marine tanks. I would like a new business card to suit.

Must include Name, company name, abn, contact number and website as well as logo (see attached).

Looking for a design that stands out, has a clean but unique appearance.

Double and single sided entries welcome

Business

• Logo

```html
<!DOCTYPE html>
<html lang="en">
<head>
<meta charset="utf-8">
<title>Corvane Freight Company – Business Card</title>
<link rel="stylesheet" href="https://fonts.googleapis.com/css2?family=Open+Sans:wght@400;600;700&display=swap">
<style>
  :root {
    --backdrop: #141414;
    --card-white: #ffffff;
    --sky: #55cbf3;
    --ocean: #1d8fd0;
    --deep: #1360ad;
    --navy-text: #1a5aa6;
    --grey-text: #555555;
    --rule: #b9b9b9;
  }
  * { box-sizing: border-box; margin: 0; padding: 0; }
  html, body {
    width: 1200px; height: 420px; overflow: hidden;
    background: var(--backdrop);
    font-family: "Open Sans", Arial, sans-serif;
  }
  .stage { position: relative; width: 1200px; height: 420px; }
  .card { position: absolute; top: 66px; width: 524px; height: 299px; overflow: hidden; }
  .card-front { left: 66px; background: var(--card-white); }
  .card-back { left: 635px; background: var(--sky); }

  .accent { position: absolute; }
  .accent-top-light { left: 214px; top: 0; width: 272px; height: 8px; background: var(--sky); }
  .accent-top-dark { left: 471px; top: 0; width: 53px; height: 13px; background: var(--deep); }
  .accent-top-dark::before { content: ""; position: absolute; left: 0; top: 0; width: 16px; height: 8px; background: var(--sky); }
  .accent-bottom-light { left: 0; top: 244px; width: 6px; height: 55px; background: var(--sky); }
  .accent-bottom-dark { left: 0; top: 262px; width: 11px; height: 37px; background: var(--deep); }

  .divider {
    position: absolute; left: 266px; top: 64px; width: 2px; height: 180px;
    background: linear-gradient(to bottom, rgba(185,185,185,0), var(--rule) 30%, var(--rule) 70%, rgba(185,185,185,0));
  }

  .brand-front {
    position: absolute; left: 20px; top: 112px; width: 230px;
    display: flex; align-items: center; gap: 10px;
    color: var(--ocean); font-weight: 600; font-size: 24px; line-height: 1.1;
  }
  .brand-mark { width: 14px; height: 14px; border-radius: 50%; background: currentColor; flex: none; }

  .contact { position: absolute; left: 284px; top: 68px; width: 230px; }
  .person-name { color: var(--deep); font-weight: 700; font-size: 17px; line-height: 22px; }
  .person-title { color: var(--grey-text); font-size: 14px; line-height: 20px; }
  .contact-line {
    display: flex; align-items: center; gap: 7px;
    color: var(--navy-text); font-size: 12.5px; line-height: 18px;
  }
  .contact-line svg { width: 10px; height: 10px; flex: none; }
  .phone-line { margin-top: 14px; }
  .address { margin-top: 22px; color: var(--navy-text); font-size: 12.5px; line-height: 19px; }

  .brand-back {
    position: absolute; left: 0; top: 0; width: 100%; height: 100%;
    display: flex; align-items: center; justify-content: center; gap: 18px;
    color: var(--card-white); font-weight: 600; font-size: 46px; line-height: 1.05; text-align: center;
  }
</style>
</head>
<body>
<main class="stage">
  <section class="card card-front" aria-label="Business card front">
    <div class="accent accent-top-light"></div>
    <div class="accent accent-top-dark"></div>
    <div class="accent accent-bottom-light"></div>
    <div class="accent accent-bottom-dark"></div>

    <div class="brand-front">
      <span class="brand-mark"></span>
      <span class="brand-name">Corvane Freight Company</span>
    </div>

    <div class="divider"></div>

    <div class="contact">
      <p class="person-name">Your Name</p>
      <p class="person-title">Title</p>
      <p class="contact-line phone-line">
        <svg viewBox="0 0 10 10" aria-hidden="true"><path d="M2 0.8 L3.6 2.9 L2.8 3.8 Q4 6.2 6.2 7.2 L7.1 6.4 L9.2 8 L8 9.4 Q3.5 9 0.6 2 Z" fill="#1a5aa6"/></svg>
        123-456-7892
      </p>
      <p class="contact-line">
        <svg viewBox="0 0 10 10" aria-hidden="true"><circle cx="5" cy="5" r="4.3" fill="none" stroke="#1a5aa6" stroke-width="1"/><ellipse cx="5" cy="5" rx="1.8" ry="4.3" fill="none" stroke="#1a5aa6" stroke-width="0.8"/><line x1="0.7" y1="5" x2="9.3" y2="5" stroke="#1a5aa6" stroke-width="0.8"/></svg>
        www.corvanefreight.com
      </p>
      <p class="address">Street Name, City Name ,<br>State, Zip Code<br>ABN: 123456789</p>
    </div>
  </section>

  <section class="card card-back" aria-label="Business card back">
    <div class="brand-back">
      <span class="brand-name">Corvane Freight<br>Company</span>
    </div>
  </section>
</main>
</body>
</html>
```